Automotive eCommerce Business looking for a business card design

Looking for a clean and simple business card design. Our company name is "Brindle Auto" and we are a company specializing in the ecommerce sales of automotive parts, specifically for pick up trucks and large SUVs. Our company colours are red, black, and white.

Feel free to use the logo provided or create a new logo that you seem fit. Looking forward to your creative ideas!

Industry/Entity Type

Automotive

Contact Information for Business Card

We were thinking of a possibly two-sided design featuring just the logo and company name on one side, and personal information on the other side. Single sided designs will be considered as well.

Font styles to use
Serif
Sans Serif
Decorative

Colors
ec1f27
ffffff
000000

Requirements
Must have
• Space for employee's name, title, phone number and email address, along with the company address and website somewhere.

```html
<!DOCTYPE html>
<html lang="en">
<head>
<meta charset="utf-8">
<title>Brindle Auto Ltd. – Business Card</title>
<link rel="stylesheet" href="https://fonts.googleapis.com/css2?family=Cinzel:wght@500&family=Roboto:wght@400;500&display=swap">
<style>
  :root {
    --brand-red: #a31f24;
    --ink: #4a4a4a;
    --ink-soft: #5a5a5a;
    --card: #f7f7f7;
    --backdrop: #e4e4e4;
  }
  * { margin: 0; padding: 0; box-sizing: border-box; }
  html, body { width: 1200px; height: 960px; overflow: hidden; }
  body { background: var(--backdrop); position: relative; font-family: "Roboto", Arial, sans-serif; }

  .card {
    position: absolute;
    left: 320px;
    width: 600px;
    height: 342px;
    background: var(--card);
    border-radius: 18px;
    box-shadow: 0 2px 6px rgba(0,0,0,0.18);
    overflow: hidden;
  }
  .card--front { top: 100px; }
  .card--back { top: 493px; }

  /* Front */
  .front-mark {
    position: absolute;
    left: 50%;
    top: 68px;
    width: 120px;
    height: 120px;
    margin-left: -60px;
    border-radius: 50%;
    background: var(--brand-red);
  }
  .front-name {
    position: absolute;
    left: 0; right: 0;
    top: 236px;
    text-align: center;
    font-family: "Cinzel", Georgia, serif;
    font-weight: 500;
    font-size: 26px;
    letter-spacing: 0.5px;
    color: var(--ink-soft);
  }
  .front-web {
    position: absolute;
    left: 0; right: 0;
    top: 298px;
    text-align: center;
    font-size: 14px;
    letter-spacing: 5px;
    color: var(--ink);
  }

  /* Back */
  .person { position: absolute; left: 34px; top: 115px; }
  .person-name {
    font-weight: 500;
    font-size: 20px;
    color: var(--brand-red);
    text-transform: uppercase;
    line-height: 24px;
  }
  .person-title {
    font-weight: 500;
    font-size: 15px;
    color: var(--ink);
    line-height: 22px;
  }
  .address {
    margin-top: 16px;
    font-size: 14.5px;
    color: var(--ink);
    line-height: 18px;
  }
  .contact-list { list-style: none; margin-top: 14px; }
  .contact-list li {
    display: flex;
    align-items: center;
    font-size: 14.5px;
    color: var(--ink);
    line-height: 19.5px;
  }
  .contact-list svg { width: 13px; height: 13px; margin-right: 10px; fill: var(--brand-red); flex: none; }

  .back-name {
    position: absolute;
    left: 256px;
    right: 0;
    top: 0;
    bottom: 0;
    display: flex;
    align-items: center;
    justify-content: center;
    font-family: "Cinzel", Georgia, serif;
    font-weight: 500;
    font-size: 40px;
    line-height: 1.15;
    text-align: center;
    color: var(--brand-red);
  }
</style>
</head>
<body>

  <section class="card card--front">
    <div class="front-mark"></div>
    <h1 class="front-name">Brindle Auto Ltd.</h1>
    <p class="front-web">www.brindleauto.com</p>
  </section>

  <section class="card card--back">
    <div class="person">
      <h2 class="person-name">Dana Whitfield</h2>
      <p class="person-title">CEO/FOUNDER</p>
      <p class="address">3318 Cedarline Drive<br>Juneau, Alaska 99801</p>
      <ul class="contact-list">
        <li>
          <svg viewBox="0 0 16 16" aria-hidden="true"><path d="M3.6 1l2.6 3-1.5 1.8c.9 2 2.5 3.6 4.5 4.5L11 8.8l3 2.6-1.4 2.6C7 14 2 9 2 3.4z"/></svg>
          907 555 0142
        </li>
        <li>
          <svg viewBox="0 0 16 16" aria-hidden="true"><path d="M4.5 1h7v14h-7zM6 2.5v9.5h4V2.5zM7.3 13h1.4v1H7.3z" fill-rule="evenodd"/></svg>
          907 555 0187
        </li>
        <li>
          <svg viewBox="0 0 16 16" aria-hidden="true"><path d="M4 2h8v4H4zM1 7h14v6h-3v-2H4v2H1zM5 12h6v3H5z"/></svg>
          907 555 0119
        </li>
        <li>
          <svg viewBox="0 0 16 16" aria-hidden="true"><path d="M1 3h14v1.2L8 9 1 4.2zM1 6l7 4.8L15 6v7H1z"/></svg>
          dana@brindleauto.com
        </li>
        <li>
          <svg viewBox="0 0 16 16" aria-hidden="true"><circle cx="8" cy="8" r="7"/></svg>
          www.brindleauto.com
        </li>
      </ul>
    </div>
    <p class="back-name">Brindle<br>Auto</p>
  </section>

</body>
</html>
```